Seeking funky, innovative business cards

I am looking to refresh our current business cards to something more engaging, visual and impactful. We are a management consultancy firm, see website (www.larkstone-partners.com.au). I've included our colour scheme, sample of the slides we use and our old business cards. We would like our cards to have icons. The card should display:- Name- Title- Mobile number- Address- Email address- Website - Company logo- Our purpose statement "We shape the finest workplaces in the land"

Contact Information for Business Card

Brennan Ulfsson
Consultant
0468 927 341
Level 3, 218 Wexley Street, Melbourne 3000
brennan@larkstone-partners.com.au
www.larkstone-partners.com.au

Purpose statement "We shape the finest workplaces in the land"
LOGO available in google images

Font styles to use
Other font styles liked:
• Open Sans Light, Bebas Neue (open to other cool foints)

Colors
ffc214
5c5c5c
f5f5f5
fefefe

Requirements
Must have
• - Name
• - Title
• - Mobile number
• - Address
• - Email address
• - Website
• - Company logo
• - Our purpose statement "We shape the finest workplaces in the land"
Nice to have
• - Icons
• - Colour (see our colour scheme"

```html
<!DOCTYPE html>
<html lang="en">
<head>
<meta charset="utf-8">
<title>Larkstone Partners – Business Card</title>
<link href="https://fonts.googleapis.com/css2?family=Lato:wght@300;400&display=swap" rel="stylesheet">
<style>
  :root {
    --backdrop: #7b7b7b;
    --card-light: #fefefe;
    --card-dark: #434847;
    --ink: #1f1f1f;
    --ink-soft: #5c5c5c;
    --accent: #ffc214;
    --accent-deep: #f7a823;
    --rule: #8a8a8a;
    --on-dark: #f5f5f5;
  }
  * { box-sizing: border-box; margin: 0; padding: 0; }
  html, body { width: 1200px; height: 1200px; overflow: hidden; }
  body {
    background: var(--backdrop);
    font-family: "Lato", sans-serif;
    position: relative;
  }
  .card {
    position: absolute;
    top: 310px;
    height: 594px;
    box-shadow: 2px 3px 5px rgba(0,0,0,0.45);
    text-align: center;
  }
  .card--front { left: 234px; width: 364px; background: var(--card-light); }
  .card--back { left: 627px; width: 370px; background: var(--card-dark); }

  .wordmark {
    position: absolute;
    left: 0; right: 0;
    display: flex;
    justify-content: center;
    align-items: center;
    gap: 12px;
    font-weight: 300;
    font-size: 54px;
    line-height: 64px;
    letter-spacing: 0.5px;
  }
  .wordmark__dot {
    width: 14px; height: 14px; border-radius: 50%;
    background: var(--accent);
  }
  .card--front .wordmark { top: 174px; color: var(--ink-soft); }
  .card--back .wordmark { top: 286px; color: var(--on-dark); }

  .person { position: absolute; top: 336px; left: 0; right: 0; }
  .person__name {
    color: var(--accent-deep);
    font-size: 22px;
    line-height: 26px;
    font-weight: 400;
    text-transform: uppercase;
    letter-spacing: 0.2px;
  }
  .person__title { color: var(--ink-soft); font-size: 17px; line-height: 20px; }

  .icon-row {
    position: absolute; top: 396px; left: 87px; width: 190px; height: 24px;
  }
  .contact {
    position: absolute; top: 430px; left: 0; right: 0;
    font-size: 17px; line-height: 22px; color: var(--ink);
  }
  .divider {
    position: absolute; top: 507px; left: 89px; width: 188px;
    border-top: 1px solid var(--rule);
  }
  .address {
    position: absolute; top: 517px; left: 0; right: 0;
    font-size: 17px; line-height: 22px; color: var(--ink);
  }
  .purpose {
    position: absolute; top: 493px; left: 0; right: 0;
    color: var(--on-dark);
    font-size: 20px; line-height: 29px;
    text-transform: uppercase;
    letter-spacing: -0.2px;
  }
</style>
</head>
<body>
  <section class="card card--front" aria-label="Card front">
    <div class="wordmark"><span class="wordmark__dot"></span>Larkstone</div>

    <div class="person">
      <h1 class="person__name">Brennan Ulfsson</h1>
      <p class="person__title">Consultant</p>
    </div>

    <svg class="icon-row" viewBox="0 0 190 24" aria-hidden="true">
      <line x1="0" y1="12" x2="53" y2="12" stroke="#8a8a8a" stroke-width="1"/>
      <line x1="137" y1="12" x2="190" y2="12" stroke="#8a8a8a" stroke-width="1"/>
      <g fill="#ffc214">
        <circle cx="67" cy="12" r="12"/>
        <circle cx="95" cy="12" r="12"/>
        <circle cx="123" cy="12" r="12"/>
      </g>
      <g fill="none" stroke="#fefefe" stroke-width="1.6" stroke-linejoin="round">
        <path d="M61 10 q6 -5 12 0 l-1 2 h-2 l-1 -1.5 h-4 l-1 1.5 h-2 z M62 13 h10 v4 h-10 z"/>
        <rect x="89" y="8" width="12" height="8"/>
        <path d="M89 8 l6 4.5 l6 -4.5"/>
        <circle cx="123" cy="12" r="6"/>
        <path d="M117 12 h12 M123 6 c-3 3 -3 9 0 12 c3 -3 3 -9 0 -12"/>
      </g>
    </svg>

    <div class="contact">
      <p>0468 927 341</p>
      <p>brennan@larkstone-partners.com.au</p>
      <p>www.larkstone-partners.com.au</p>
    </div>
    <div class="divider"></div>
    <p class="address">Level 3, 218 Wexley<br>Street, Melbourne 3000</p>
  </section>

  <section class="card card--back" aria-label="Card back">
    <div class="wordmark"><span class="wordmark__dot"></span>Larkstone</div>
    <p class="purpose">We shape the finest<br>workplaces in the land</p>
  </section>
</body>
</html>
```